Executive Business Card for Healthcare Company [Need Today]

I need a business card design for a healthcare company. The only branding the company has thus far is a logo. The cards will be utilized by company executives. The design I envision will be vibrant and appealing but with a corporate feel. They shouldn't be too casual or playful. I would like to complete this project TODAY if possible.

Target Market(s)

Healthcare vendors, other executives in healthcare and pharmaceuticals

Industry/Entity Type

Pharmaceutical

Contact Information for Business Card

See attachment

Font styles to use
Serif
Sans Serif

Colors

Designer to choose colors to be used in the design.

```html
<!DOCTYPE html>
<html lang="en">
<head>
<meta charset="utf-8">
<title>Calder Therapeutics – Business Card</title>
<link rel="stylesheet" href="https://fonts.googleapis.com/css2?family=Arimo:wght@400;700&display=swap">
<style>
  :root {
    --page: #e9eaeb;
    --card: #ffffff;
    --card-back: #f4f5f5;
    --teal: #2aa5b3;
    --teal-deep: #178a96;
    --green: #4fb08f;
    --ink: #3a3d40;
    --muted: #7b7f83;
    --rule: #b9bcbf;
    --band-edge: #8e9296;
    --faint: #e4e6e7;
  }
  * { box-sizing: border-box; margin: 0; padding: 0; }
  html, body { width: 1200px; height: 726px; overflow: hidden; }
  body {
    background: var(--page);
    font-family: "Arimo", Arial, sans-serif;
    color: var(--ink);
    display: flex;
    align-items: center;
    justify-content: center;
    gap: 40px;
  }
  .card {
    position: relative;
    width: 530px;
    height: 303px;
    background: var(--card);
    box-shadow: 0 6px 18px rgba(0,0,0,.12);
    overflow: hidden;
  }
  .brand {
    display: flex;
    align-items: center;
    gap: 12px;
  }
  .brand-dot {
    width: 58px; height: 58px;
    border: 3px solid var(--green);
    border-radius: 50%;
    flex: none;
  }
  .brand-rule {
    width: 1px; height: 50px;
    background: var(--rule);
  }
  .brand-name {
    font-size: 30px;
    font-weight: 400;
    color: var(--teal);
    line-height: 1.05;
    letter-spacing: .5px;
  }
  /* front */
  .card-front .brand {
    position: absolute;
    left: 70px; top: 100px;
  }
  .card-front .website {
    position: absolute;
    left: 0; right: 0; bottom: 52px;
    text-align: center;
    font-size: 13px;
    letter-spacing: 4px;
    color: var(--ink);
  }
  .website .domain { color: var(--teal); }
  /* back */
  .card-back { background: var(--card-back); }
  .side-band {
    position: absolute;
    left: 0; top: 0; bottom: 0;
    width: 52px;
    background: linear-gradient(180deg, var(--teal-deep), var(--green));
  }
  .side-edge {
    position: absolute;
    left: 52px; top: 0; bottom: 0;
    width: 10px;
    background: linear-gradient(180deg, #6d7175, #a9adb0);
  }
  .watermark {
    position: absolute;
    right: -40px; top: 40px;
    width: 230px; height: 230px;
    border: 4px solid var(--faint);
    border-radius: 50%;
  }
  .card-back .brand {
    position: absolute;
    left: 86px; top: 30px;
  }
  .card-back .brand-dot { width: 50px; height: 50px; }
  .card-back .brand-name { font-size: 25px; }
  .person {
    position: absolute;
    left: 92px; top: 130px;
  }
  .person-name {
    font-size: 21px;
    font-weight: 700;
    color: var(--teal);
  }
  .person-title {
    margin-top: 4px;
    font-size: 9.5px;
    color: var(--muted);
    padding-left: 14px;
  }
  .contacts {
    position: absolute;
    left: 92px; top: 190px;
    list-style: none;
    font-size: 13px;
    color: var(--ink);
  }
  .contacts li {
    display: flex;
    align-items: center;
    gap: 8px;
    height: 19px;
  }
  .contacts svg { width: 12px; height: 12px; fill: var(--muted); flex: none; }
  .contacts .email-domain { color: var(--teal); }
  .contacts .address { padding-left: 0; margin-top: 2px; }
</style>
</head>
<body>
  <section class="card card-front" aria-label="Card front">
    <div class="brand">
      <span class="brand-dot"></span>
      <span class="brand-rule"></span>
      <span class="brand-name">Calder Therapeutics</span>
    </div>
    <p class="website">www.<span class="domain">calderrx</span>.com</p>
  </section>

  <section class="card card-back" aria-label="Card back">
    <div class="side-band"></div>
    <div class="side-edge"></div>
    <div class="watermark"></div>
    <div class="brand">
      <span class="brand-dot"></span>
      <span class="brand-rule"></span>
      <span class="brand-name">Calder Therapeutics</span>
    </div>
    <div class="person">
      <h1 class="person-name">Martin Hale</h1>
      <p class="person-title">Senior Director of Marketing</p>
    </div>
    <ul class="contacts">
      <li>
        <svg viewBox="0 0 12 12" aria-hidden="true"><path d="M1 4c0-2 1.5-2.5 2-2.5h6c.5 0 2 .5 2 2.5v.5H8.5V3h-5v1.5H1z"/><rect x="2.5" y="6" width="7" height="5" rx="1"/></svg>
        555-201-4470
      </li>
      <li>
        <svg viewBox="0 0 12 12" aria-hidden="true"><rect x="3" y="0.5" width="6" height="11" rx="1"/><rect x="4" y="2" width="4" height="7" fill="#f4f5f5"/></svg>
        555-318-2096
      </li>
      <li>
        <svg viewBox="0 0 12 12" aria-hidden="true"><circle cx="6" cy="6" r="5.5"/><path d="M.8 6h10.4M6 .5v11M6 .5c-3 3-3 8 0 11M6 .5c3 3 3 8 0 11" stroke="#f4f5f5" stroke-width=".9" fill="none"/></svg>
        mhale@<span class="email-domain">calderrx</span>.com
      </li>
      <li class="address">118 Orchard Avenue Dalton, GA 30720</li>
    </ul>
  </section>
</body>
</html>
```